Tall ridge firewood

It a new firewood outlet in Kestrel Creek NSW that will only sell top hardwood firewood (ironbark , red gum, grey gum, an box mix. I would like to see a web page the we can do order online payment for delivery. It will all so need to have photos of the firewood. I all so have logo for tall ridge firewood
Must have a modem look but easy to use I would like to see a black back ground of some sort.

Here are some other firewood web pages for ideas and firewood info
http://www.example-logpile.com.au
http://www.example-stackwood.com.au
http://www.example-splitlog.com.au
http://www.example-kendaltimber.com.au/firewood

Industry/Entity Type

Firewood

```html
<!DOCTYPE html>
<html lang="en">
<head>
<meta charset="utf-8">
<title>Tall ridge firewood</title>
<link rel="stylesheet" href="https://fonts.googleapis.com/css2?family=Roboto+Condensed:wght@400;700&family=Arimo:wght@400;700&display=swap">
<style>
:root{
  --dark:#1b1b1b;
  --blue:#2f8be0;
  --blue-deep:#1f6fc2;
  --orange:#ff6a00;
  --text:#666;
  --ink:#222;
  --light:#f2f2f2;
  --tile:#efefef;
  --white:#fff;
  --soft-blue:#9fd0ff;
}
*{margin:0;padding:0;box-sizing:border-box}
html,body{width:1038px;height:1200px;overflow:hidden;background:var(--white)}
body{position:relative;font-family:"Arimo",Arial,sans-serif;color:var(--text)}
.abs{position:absolute}
.header{left:0;top:0;width:1038px;height:558px;background:linear-gradient(90deg,#141414,#242424 30%,#1c1c1c 60%,#262626 85%,#161616)}
.logo{left:140px;top:2px;width:186px;height:155px;background:var(--white);display:flex;flex-direction:column;align-items:center;justify-content:center;gap:10px}
.logo-mark{width:70px;height:70px;border-radius:50%;background:var(--blue-deep)}
.logo-name{font-family:"Roboto Condensed",sans-serif;font-weight:700;font-size:16px;color:var(--blue-deep);text-transform:uppercase}
.call{left:522px;top:61px;color:var(--soft-blue);font-size:11px}
.call strong{display:block;color:var(--white);font-size:19px;margin-top:2px}
.address{left:716px;top:62px;color:var(--white);font-size:11px;line-height:13px}
.address .label{color:var(--soft-blue)}
.address u{color:var(--white)}
.nav{left:0;top:177px;width:1038px;height:29px;background:var(--blue)}
.nav ul{list-style:none;position:absolute;left:140px;top:0;display:flex;height:29px}
.nav li{font-family:"Roboto Condensed",sans-serif;font-size:12px;color:var(--white);display:flex;align-items:center;justify-content:center;border-right:1px solid #5aa3e8;height:29px}
.nav li.active{background:linear-gradient(#3a3a3a,#111);border:none}
.nav li.order{background:var(--orange);font-weight:700;border:none}
.hero{left:140px;top:206px;width:759px;height:352px;background:radial-gradient(ellipse at 55% 60%,#ffb13b 0%,#d8621a 18%,#7a4026 38%,#4a3a33 60%,#2a2622 100%)}
.arrow{top:370px;width:30px;height:24px;background:var(--white);display:flex;align-items:center;justify-content:center}
.caption{left:385px;top:366px;width:268px;height:32px;background:var(--blue-deep);border:1px solid var(--white);color:var(--white);font-size:18px;display:flex;align-items:center;justify-content:center}
.caption b{margin:0 5px}
.tile{top:583px;width:156px}
.tile .photo{height:118px}
.tile .label{height:43px;background:var(--tile);font-family:"Roboto Condensed",sans-serif;font-size:17px;color:var(--ink);display:flex;align-items:center;justify-content:center;text-transform:uppercase}
.tile.active .label{background:var(--blue-deep);color:var(--white)}
.col{top:792px}
.col h2{font-family:"Roboto Condensed",sans-serif;font-weight:400;font-size:20px;color:var(--blue-deep);margin-bottom:20px}
.col p{font-size:10px;line-height:12px;margin-bottom:12px}
.divider{top:793px;width:1px;height:184px;background:#e0e0e0}
.list{list-style:none}
.list li{display:flex;gap:10px;font-size:10px;line-height:12px;margin-bottom:14px}
.list li .n{font-family:"Roboto Condensed",sans-serif;font-weight:700;font-size:18px;color:var(--ink);width:22px;line-height:18px}
.btn{top:957px;height:21px;padding:0 11px;background:linear-gradient(#3a3a3a,#0d0d0d);color:var(--white);font-size:10px;display:flex;align-items:center}
.footer{left:0;top:1011px;width:1038px;height:161px;background:var(--light)}
.f-col{top:1030px}
.f-col h3{font-size:10px;font-weight:700;color:var(--blue-deep);margin-bottom:9px}
.f-col ul{list-style:none;font-size:9.5px;color:var(--text);line-height:13.7px}
.f-col li::before{content:"»";margin-right:6px}
.cards{display:flex;gap:10px;margin-bottom:28px}
.cards span{width:30px;height:20px;background:#ddd;border:1px solid #bbb}
.social{display:flex;gap:4px}
.social span{width:23px;height:23px;background:#9a9a9a}
.client{left:654px;top:1026px;width:246px}
.client h3{font-size:14px;color:var(--blue-deep);margin-bottom:6px}
.client p{font-size:10px;line-height:12px;margin-bottom:12px}
.client .by{font-size:10px}
.client .more{display:inline-block;margin-top:14px;background:var(--blue);color:var(--white);font-size:10px;padding:5px 12px}
.copy{left:0;top:1172px;width:1038px;height:28px;background:var(--dark);color:var(--white);font-size:9.5px;display:flex;align-items:center;justify-content:center}
</style>
</head>
<body>
<div class="abs header"></div>
<div class="abs logo"><span class="logo-mark"></span><span class="logo-name">Tall ridge firewood</span></div>
<div class="abs call">Call us<strong>0400 555 019</strong></div>
<div class="abs address">215, Lorem Ipsum is simply dummy<br>Kestrel Creek NSW<br><span class="label">Email - </span><u>info@tallridgefirewood.com</u></div>

<nav class="abs nav"><ul>
  <li class="active" style="width:80px">HOME</li>
  <li style="width:88px">ABOUT US</li>
  <li style="width:91px">PRODUCTS</li>
  <li style="width:109px">ACCESSORIES</li>
  <li style="width:88px">DELIVERY</li>
  <li style="width:73px">FAQ`S</li>
  <li style="width:124px">CONTACT US</li>
  <li class="order" style="width:106px">ORDER ONLINE</li>
</ul></nav>

<div class="abs hero" role="img" aria-label="Photo of a hardwood fire burning in a stone fireplace"></div>
<div class="abs arrow" style="left:140px"><svg width="12" height="14" viewBox="0 0 12 14"><path d="M9 1L3 7l6 6" fill="none" stroke="#1f6fc2" stroke-width="3"/></svg></div>
<div class="abs arrow" style="left:869px"><svg width="12" height="14" viewBox="0 0 12 14"><path d="M3 1l6 6-6 6" fill="none" stroke="#1f6fc2" stroke-width="3"/></svg></div>
<div class="abs caption">TOP <b>HARDWOOD</b> FIREWOOD</div>

<div class="abs tile active" style="left:140px"><div class="photo" role="img" aria-label="Photo of split ironbark logs" style="background:linear-gradient(135deg,#3a2414,#a5643a 50%,#2a1a10)"></div><div class="label">Ironbark</div></div>
<div class="abs tile" style="left:341px"><div class="photo" role="img" aria-label="Photo of a pile of red gum firewood" style="background:linear-gradient(135deg,#a86a55,#d7a793 50%,#8a5240)"></div><div class="label">Red Gum</div></div>
<div class="abs tile" style="left:542px"><div class="photo" role="img" aria-label="Photo of a pile of grey gum firewood" style="background:linear-gradient(135deg,#5f6468,#a6abae 50%,#4e5256)"></div><div class="label">Grey Gum</div></div>
<div class="abs tile" style="left:743px"><div class="photo" role="img" aria-label="Photo of box mix logs burning in a fireplace" style="background:radial-gradient(ellipse at 55% 50%,#ffb040,#b4521c 30%,#3a2a22 65%,#1e1a18)"></div><div class="label">Box Mix</div></div>

<section class="abs col" style="left:140px;width:200px">
  <h2>WELCOME TO OUR SITE</h2>
  <p>Lorem ipsum dolor sit amet, consectetur adipisicing elit, sed do eiusmod tempor incididunt ut labore et dolore magna aliqua. Ut enim ad minim veniam, quis nostrud exercitation ullamco.</p>
  <p>Duis aute irure dolor in reprehenderit in voluptate velit esse cillum dolore eu fugiat nulla pariatur ...</p>
</section>
<div class="abs divider" style="left:378px"></div>
<section class="abs col" style="left:420px;width:210px">
  <h2>WHY CHOOSE US?</h2>
  <ul class="list">
    <li><svg width="11" height="10" viewBox="0 0 11 10"><path d="M1 5l3 3 6-7" fill="none" stroke="#999" stroke-width="2"/></svg><span>Lorem ipsum dolor sit amet, consectetur adipisicing elit.</span></li>
    <li><svg width="11" height="10" viewBox="0 0 11 10"><path d="M1 5l3 3 6-7" fill="none" stroke="#999" stroke-width="2"/></svg><span>Lorem ipsum dolor sit amet, consectetur adipisicing elit.</span></li>
    <li><svg width="11" height="10" viewBox="0 0 11 10"><path d="M1 5l3 3 6-7" fill="none" stroke="#999" stroke-width="2"/></svg><span>Lorem ipsum dolor sit amet, consectetur adipisicing elit.</span></li>
  </ul>
</section>
<div class="abs divider" style="left:655px"></div>
<section class="abs col" style="left:691px;width:212px">
  <h2>LATEST NEWS</h2>
  <ul class="list">
    <li><span class="n">01</span><span>Lorem ipsum dolor sit amet, consectetur adipisicing elit.</span></li>
    <li><span class="n">02</span><span>Lorem ipsum dolor sit amet, consectetur adipisicing elit.</span></li>
    <li><span class="n">03</span><span>Lorem ipsum dolor sit amet, consectetur adipisicing elit.</span></li>
  </ul>
</section>
<a class="abs btn" style="left:140px">READ MORE</a>
<a class="abs btn" style="left:420px">READ MORE</a>
<a class="abs btn" style="left:691px">VIEW ALL</a>

<footer class="abs footer"></footer>
<div class="abs f-col" style="left:140px"><h3>NAVIGATION</h3><ul><li>Home</li><li>About Us</li><li>Products</li><li>Accessories</li><li>Contact Us</li></ul></div>
<div class="abs f-col" style="left:283px"><h3>ORDER ONLINE</h3><ul><li>Terms &amp; Conditions</li><li>Delivery</li><li>Faq`s</li></ul></div>
<div class="abs f-col" style="left:453px"><h3>PAYMENT OPTION</h3><div class="cards"><span></span><span></span><span></span></div><h3>FOLLOW US ON</h3><div class="social"><span></span><span></span><span></span><span></span></div></div>
<div class="abs client"><h3>Happy Client`s</h3><p>Lorem ipsum dolor sit amet, consectetur adipisicing elit, sed do eiusmod tempor incididunt ut labore et dolore magna aliqua.</p><div class="by"><b>Sam</b>. 15/06/13</div><a class="more">READ MORE</a></div>
<div class="abs copy">COPYRIGHT © TALL RIDGE FIREWOOD 2013. ALL RIGHT RESERVED.</div>
</body>
</html>
```